MV Decor

There is a sample provided with the arabic text of the business card. please copy paste the same text and the same Logo (The two triangles) Just try to incorproate the Brown background attached (you are free to change the colors) Id like the colors to be mainly shades of black and red.

```html
<!DOCTYPE html>
<html lang="ar">
<head>
<meta charset="utf-8">
<title>MV Decor — Business Card</title>
<link href="https://fonts.googleapis.com/css2?family=Aref+Ruqaa:wght@400;700&family=Tajawal:wght@300;400;700&family=Roboto:wght@400&display=swap" rel="stylesheet">
<style>
  :root {
    --backdrop: #5e3d29;
    --ink: #252723;
    --red: #d11f48;
    --red-deep: #b8173c;
    --red-light: #e0335a;
    --white: #ffffff;
  }
  html, body {
    margin: 0;
    width: 1125px;
    height: 1200px;
    overflow: hidden;
    background: var(--backdrop);
  }
  .card {
    position: absolute;
    left: 171px;
    width: 826px;
    height: 472px;
    overflow: hidden;
    box-shadow: 0 3px 8px rgba(0,0,0,0.45);
  }
  .card--front { top: 106px; }
  .card--back { top: 639px; }

  .red-field {
    position: absolute;
    inset: 0;
    background: radial-gradient(ellipse at 65% 40%, var(--red-light) 0%, var(--red) 45%, var(--red-deep) 100%);
  }
  .front-shape {
    position: absolute;
    inset: 0;
  }

  .owner {
    position: absolute;
    right: 548px;
    top: 52px;
    direction: rtl;
    text-align: right;
    color: var(--white);
    font-family: "Aref Ruqaa", serif;
  }
  .owner__name {
    font-size: 29px;
    font-weight: 700;
    line-height: 1.1;
    white-space: nowrap;
  }
  .owner__title {
    font-size: 19px;
    line-height: 1.2;
    margin-right: 60px;
  }
  .phone {
    position: absolute;
    left: 45px;
    top: 150px;
    display: flex;
    align-items: center;
    gap: 6px;
    color: var(--white);
    font-family: "Roboto", sans-serif;
    font-size: 22px;
  }
  .phone svg { width: 18px; height: 18px; }

  .credentials {
    position: absolute;
    direction: rtl;
    font-family: "Tajawal", sans-serif;
    font-weight: 400;
    color: var(--white);
    margin: 0;
    padding: 0;
    list-style: none;
  }
  .credentials--front {
    right: 548px;
    top: 303px;
    font-size: 21px;
    line-height: 27.5px;
    letter-spacing: 0.5px;
  }
  .credentials--back {
    left: 392px;
    width: 320px;
    top: 100px;
    font-size: 25px;
    line-height: 33px;
    letter-spacing: 0.5px;
  }
  .credentials--back li {
    display: flex;
    align-items: center;
    gap: 9px;
  }
  .bullet {
    width: 8px;
    height: 8px;
    border-radius: 50%;
    background: var(--white);
    flex: none;
  }

  .brand {
    position: absolute;
    font-family: "Tajawal", sans-serif;
    font-weight: 700;
    color: var(--white);
    letter-spacing: 2px;
    white-space: nowrap;
  }
  .brand--front {
    left: 537px;
    width: 183px;
    top: 204px;
    font-size: 40px;
    text-align: center;
  }
  .brand--back {
    left: 118px;
    width: 262px;
    top: 210px;
    font-size: 50px;
    text-align: center;
  }
</style>
</head>
<body>

<section class="card card--front">
  <div class="red-field" role="img" aria-label="Red field with a soft pattern of small squares"></div>
  <svg class="front-shape" viewBox="0 0 826 472" width="826" height="472" aria-hidden="true">
    <polygon points="0,0 517,0 356,234 517,472 0,472" fill="var(--ink)"/>
    <polyline points="532,0 364,234 532,472" fill="none" stroke="var(--white)" stroke-width="4"/>
  </svg>

  <div class="owner">
    <div class="owner__name">المهندس / سامي يوسف الناصر</div>
    <div class="owner__title">أستاذ جامعي</div>
  </div>

  <div class="phone">
    <svg viewBox="0 0 24 24" aria-hidden="true"><path fill="#fff" d="M6.6 10.8a15.2 15.2 0 0 0 6.6 6.6l2.2-2.2a1 1 0 0 1 1-.25 11.4 11.4 0 0 0 3.6.57 1 1 0 0 1 1 1V20a1 1 0 0 1-1 1A17 17 0 0 1 3 4a1 1 0 0 1 1-1h3.5a1 1 0 0 1 1 1c0 1.25.2 2.45.57 3.57a1 1 0 0 1-.25 1z"/></svg>
    <span>38120455 / 66402918</span>
  </div>

  <ul class="credentials credentials--front">
    <li>ماجستير هندسة ديكور</li>
    <li>دبلوم عالي فن تشكيلي</li>
    <li>جامعة الفنون (باريس)</li>
    <li>استشارات هندسية - فنية</li>
  </ul>

  <div class="brand brand--front">MV DECOR</div>
</section>

<section class="card card--back">
  <div class="red-field" role="img" aria-label="Red field with a soft pattern of small squares"></div>

  <div class="brand brand--back">MV DECOR</div>

  <ul class="credentials credentials--back">
    <li><span>ماجستير هندسة ديكور</span><span class="bullet"></span></li>
    <li><span>دبلوم عالي فن تشكيلي</span><span class="bullet"></span></li>
    <li><span>جامعة الفنون (باريس)</span><span class="bullet"></span></li>
    <li><span>استشارات هندسية - فنية</span><span class="bullet"></span></li>
    <li><span>ماجستير هندسة ديكور</span><span class="bullet"></span></li>
    <li><span>دبلوم عالي فن تشكيلي</span><span class="bullet"></span></li>
    <li><span>جامعة الفنون (باريس)</span><span class="bullet"></span></li>
    <li><span>استشارات هندسية - فنية</span><span class="bullet"></span></li>
  </ul>
</section>

</body>
</html>
```